Website Design for Employee Moral and Happiness Company

Looking for a clean website design that explains our features in a step by step manner so our visitors know exactly what our site does before logging in.

The site is called "Velrato". See logo design and video for a sample of style and an overview of what we do.

Target Market(s)

Business owners that are looking to retain employees.

Number of Pages Required

1 page

```html
<!DOCTYPE html>
<html lang="en">
<head>
<meta charset="utf-8">
<title>Velrato — Employee Happiness</title>
<link href="https://fonts.googleapis.com/css2?family=Lato:ital,wght@0,400;0,700;0,900;1,400&display=swap" rel="stylesheet">
<style>
:root{
  --orange:#e8531e;
  --dark:#222222;
  --ink:#333333;
  --muted:#555555;
  --grey-bg:#f0f0f0;
  --line:#d6d6d6;
  --chip:#444a4f;
  --testi:#3b3d40;
  --footer:#141414;
  --white:#ffffff;
  --teal:#1f4f55;
  --navy:#33406e;
  --skin:#c9987a;
  --suit:#2c2f38;
}
*{margin:0;padding:0;box-sizing:border-box}
html,body{width:1200px;height:4084px;overflow:hidden}
body{font-family:'Lato',sans-serif;color:var(--ink);background:var(--white);position:relative}
.wrap{width:1050px;margin:0 auto;position:relative}
a{color:inherit;text-decoration:none}
.btn{display:inline-flex;align-items:center;justify-content:center;background:var(--orange);color:var(--white);font-weight:700;font-size:18px}
.section-title{text-align:center;font-size:42px;font-weight:700;color:var(--dark)}
.section-title::after{content:"";display:block;width:70px;height:3px;background:var(--orange);margin:18px auto 0}
.lead{text-align:center;font-size:13px;color:var(--muted)}

/* header */
.site-header{height:76px}
.site-header .wrap{display:flex;align-items:center;justify-content:space-between;height:76px}
.logo{font-size:44px;font-weight:900;color:var(--dark);letter-spacing:1px}
.nav{display:flex;gap:33px;font-size:14px;font-weight:700;color:var(--dark)}
.nav .active{color:var(--orange)}

/* hero */
.hero{position:relative;height:640px;overflow:hidden}
.hero-photo{position:absolute;inset:0;background:
  radial-gradient(ellipse 160px 200px at 120px 330px,rgba(140,92,66,.85),transparent 70%),
  radial-gradient(ellipse 150px 190px at 390px 360px,rgba(214,170,140,.8),transparent 70%),
  radial-gradient(ellipse 150px 190px at 830px 380px,rgba(110,72,52,.85),transparent 70%),
  radial-gradient(ellipse 160px 200px at 1090px 340px,rgba(205,160,130,.8),transparent 70%),
  radial-gradient(ellipse 700px 260px at 600px 640px,rgba(30,32,40,.9),transparent 75%),
  linear-gradient(180deg,#c8ccd2 0%,#9a9ea6 35%,#5a5d66 70%,#2c2e35 100%)}
.hero-photo::after{content:"";position:absolute;inset:0;background:rgba(0,0,0,.28)}
.hero-copy{position:absolute;top:205px;left:0;right:0;text-align:center;color:var(--white)}
.hero-copy h1{font-size:70px;font-weight:900}
.hero-copy p{font-size:20px;font-weight:700;line-height:28px;width:620px;margin:6px auto 0}
.hero-copy .btn{width:186px;height:48px;margin-top:20px}
.dots{position:absolute;top:672px;left:0;right:0;display:flex;justify-content:center;gap:10px;top:596px}
.dots span{width:10px;height:10px;border-radius:50%;background:rgba(255,255,255,.35)}
.dots span.on{background:var(--orange)}

/* services */
.services{height:547px;padding-top:44px}
.cards{display:flex;justify-content:space-between;margin-top:85px}
.card{width:331px;height:264px;border:2px solid var(--line);text-align:center;position:relative;padding-top:70px}
.card .badge{position:absolute;top:-50px;left:50%;margin-left:-52px;width:104px;height:104px;border-radius:50%;background:var(--chip);border:5px solid var(--white);box-shadow:0 0 0 2px var(--line);display:flex;align-items:center;justify-content:center}
.card.featured .badge{background:var(--dark)}
.card h3{font-size:22px;color:var(--orange);font-weight:700}
.card p{font-size:13.5px;line-height:25px;color:var(--muted);padding:10px 26px 0}
.card .btn-dark{display:inline-flex;width:117px;height:38px;align-items:center;justify-content:center;background:var(--chip);color:var(--white);font-weight:700;font-size:15px;margin-top:14px}
.card.featured{background:var(--orange);border-color:var(--orange)}
.card.featured h3,.card.featured p{color:var(--white)}
.card.featured .btn-dark{background:transparent;border:2px solid var(--white)}

/* about */
.about{display:flex;height:420px}
.about-media{width:587px;height:420px;position:relative;overflow:hidden;background:
  radial-gradient(circle 230px at 290px 40px,var(--teal) 0 98%,transparent 100%),
  radial-gradient(circle 270px at 290px 40px,#243846 0 98%,transparent 100%),
  linear-gradient(180deg,#5e5f66 0%,#4f5058 55%,var(--navy) 56%,#2b3560 100%)}
.play{position:absolute;left:256px;top:174px}
.about-body{flex:1;background:var(--grey-bg);padding:58px 72px 0 27px}
.about-body h2{font-size:44px;font-weight:700;color:var(--dark)}
.about-body p{font-size:14px;line-height:26px;color:var(--muted);margin-top:20px}
.about-body .btn{width:187px;height:47px;margin-top:26px}

/* team */
.team{height:557px;padding-top:48px;position:relative}
.people{display:flex;justify-content:space-between;margin-top:60px;padding:0}
.person{width:242px;text-align:center;position:relative;height:330px}
.person .portrait{width:186px;height:186px;border-radius:50%;margin:0 auto;background:
  radial-gradient(ellipse 55px 68px at 50% 40%,var(--skin),transparent 75%),
  linear-gradient(180deg,#e9e7e4 0%,#d4d1cd 60%,var(--suit) 61%,#1d2027 100%)}
.person.p2 .portrait{background:radial-gradient(ellipse 55px 68px at 50% 40%,#d8a88a,transparent 75%),linear-gradient(180deg,#e2e2e2 0%,#cfcfcf 60%,#2a2e3a 61%,#1b1e26 100%)}
.person.p3 .portrait{background:radial-gradient(ellipse 70px 80px at 50% 40%,#e6c08f,transparent 75%),radial-gradient(ellipse 58px 66px at 50% 42%,#efc3a5,transparent 75%),linear-gradient(180deg,#eeeeee 0%,#e0e0e0 62%,#f4f4f4 63%,#d9d9d9 100%)}
.person.p4 .portrait{background:radial-gradient(ellipse 55px 68px at 50% 40%,#d5a286,transparent 75%),linear-gradient(180deg,#ededed 0%,#d8d8d8 60%,#5d6f82 61%,#3c4a5a 100%)}
.person h4{font-size:21px;color:var(--orange);font-weight:700;margin-top:20px}
.person p{font-size:13.5px;line-height:22px;color:var(--muted);padding:8px 14px 0}
.person.featured{background:var(--orange);height:242px;margin-top:86px;padding-top:112px}
.person.featured .portrait{position:absolute;top:-86px;left:28px;border:4px solid var(--white)}
.person.featured h4,.person.featured p{color:var(--white)}
.person.featured h4{margin-top:0}
.arrow{position:absolute;top:248px}

/* clients */
.clients{background:var(--grey-bg);height:336px;padding-top:46px}
.clients .lead{margin-top:30px}
.logos{display:flex;justify-content:space-between;margin-top:30px}
.logos div{width:202px;height:78px;background:var(--white);border:1px solid #e2e2e2;display:flex;align-items:center;justify-content:center;gap:10px;font-size:28px;font-weight:700;color:#3a3a3a}
.logos i{width:20px;height:20px;border-radius:50%;background:var(--orange);display:block}

/* testimonials */
.testimonials{height:478px;position:relative;color:var(--white);text-align:center;padding-top:48px;background:
  radial-gradient(ellipse 120px 260px at 90px 380px,rgba(20,20,22,.7),transparent 70%),
  radial-gradient(ellipse 120px 260px at 330px 400px,rgba(20,20,22,.6),transparent 70%),
  radial-gradient(ellipse 120px 260px at 870px 390px,rgba(20,20,22,.6),transparent 70%),
  radial-gradient(ellipse 120px 260px at 1110px 380px,rgba(20,20,22,.7),transparent 70%),
  linear-gradient(180deg,#55575b 0%,#3e4044 50%,#2e3033 100%)}
.testimonials h2{font-size:42px;font-weight:700}
.testimonials .name{font-size:20px;margin-top:36px}
.testimonials blockquote{font-style:italic;font-size:19px;line-height:36px;width:850px;margin:10px auto 0;color:#e6e6e6}
.avatar{width:100px;height:100px;border-radius:50%;border:4px solid var(--white);margin:26px auto 0;background:radial-gradient(ellipse 28px 34px at 50% 42%,#d9ad92,transparent 75%),linear-gradient(180deg,#f2f2f2 0%,#e4e4e4 68%,#3a3a3a 69%,#222 100%)}
.testimonials .arrow{top:210px}

/* blog */
.blog{height:682px;padding-top:40px}
.blog .lead{margin-top:30px}
.posts{display:flex;justify-content:space-between;margin-top:33px}
.post{width:331px}
.post .thumb{height:198px;position:relative}
.post.b1 .thumb{background:radial-gradient(ellipse 60px 70px at 80px 150px,#3b4656,transparent 75%),radial-gradient(ellipse 50px 90px at 150px 90px,#e8e3da,transparent 75%),linear-gradient(120deg,#a3916f 0%,#d9cfbe 40%,#c9b48e 70%,#6b5a46 100%)}
.post.b2 .thumb{background:radial-gradient(ellipse 60px 80px at 160px 110px,#e8c07a,transparent 75%),radial-gradient(ellipse 50px 80px at 250px 130px,#6b5a3a,transparent 75%),linear-gradient(120deg,#3c3a3a 0%,#b9a79a 45%,#8c7f76 75%,#4c4643 100%)}
.post.b3 .thumb{background:radial-gradient(ellipse 60px 80px at 100px 110px,#364a6a,transparent 75%),radial-gradient(ellipse 60px 80px at 250px 120px,#5c6a7c,transparent 75%),linear-gradient(120deg,#6b5c4c 0%,#cdb9a2 45%,#9a8878 75%,#3f3a36 100%)}
.post .date{position:absolute;left:0;bottom:0;width:70px;height:78px;background:var(--orange);color:var(--white);text-align:center;font-weight:700;padding-top:6px}
.post .date span{display:block;font-size:17px}
.post .date strong{display:block;font-size:38px;line-height:40px;font-weight:700}
.post h3{font-size:23px;font-weight:700;color:var(--dark);margin-top:22px}
.post p{font-size:13.5px;line-height:22px;color:var(--muted);margin-top:12px}
.blog .cta{text-align:center;margin-top:46px}
.blog .cta .btn{width:180px;height:50px}

/* footer */
.site-footer{height:290px;background:var(--footer);color:#d8d8d8}
.site-footer .wrap{display:flex;padding-top:54px;height:290px}
.foot-logo{width:285px;font-size:52px;font-weight:900;color:var(--white);padding-top:62px;letter-spacing:1px}
.foot-col h5{color:var(--orange);font-size:16px;font-weight:700;margin-bottom:8px}
.sitemap{width:230px}
.sitemap li{list-style:none;font-size:13px;line-height:26px}
.contact{width:295px;font-size:13px}
.contact li{list-style:none;display:flex;gap:16px;line-height:20px;margin-bottom:10px}
.contact svg{flex:none;margin-top:4px}
.contact .map{color:var(--orange);font-size:13px}
.subscribe{flex:1}
.subscribe .field{height:40px;background:var(--white);color:#666;font-size:13px;padding:12px 12px}
.subscribe .btn{width:92px;height:40px;font-size:14px;float:right;margin-top:14px}
.bottom-bar{height:58px;background:#000;color:#d8d8d8}
.bottom-bar .wrap{display:flex;justify-content:space-between;align-items:center;height:58px;font-size:13px}
.social{display:flex;gap:16px;align-items:center}
.social span{width:20px;height:20px;border:2px solid #cfcfcf;border-radius:4px;display:block}
</style>
</head>
<body>

<header class="site-header">
  <div class="wrap">
    <a class="logo" href="#">Velrato</a>
    <nav class="nav">
      <a class="active" href="#">HOME</a><a href="#">WHAT WE DO</a><a href="#">WHO WE ARE</a><a href="#">BLOG</a><a href="#">CAREERS</a><a href="#">CONTACT US</a>
    </nav>
  </div>
</header>

<section class="hero">
  <div class="hero-photo" role="img" aria-label="Photo of a cheering team of colleagues raising their fists"></div>
  <div class="hero-copy">
    <h1>Welcome to Velrato</h1>
    <p>Happier teams stay longer. See how your people really feel and act before they walk out the door..</p>
    <a class="btn" href="#">Read More</a>
  </div>
  <div class="dots"><span class="on"></span><span></span><span></span><span></span></div>
</section>

<section class="services">
  <div class="wrap">
    <h2 class="section-title">Our Services</h2>
    <div class="cards">
      <div class="card featured">
        <div class="badge"><svg width="50" height="50" viewBox="0 0 50 50" fill="none" stroke="#fff" stroke-width="2"><circle cx="25" cy="15" r="6"/><circle cx="12" cy="20" r="4"/><circle cx="38" cy="20" r="4"/><path d="M14 40v-8a11 11 0 0 1 22 0v8M4 38v-5a8 8 0 0 1 8-8M46 38v-5a8 8 0 0 0-8-8"/></svg></div>
        <h3>1. Pulse Surveys</h3>
        <p>Send short weekly check-ins that take your staff under a minute and show how every team is feeling right now ..</p>
        <a class="btn-dark" href="#">Read More</a>
      </div>
      <div class="card">
        <div class="badge"><svg width="50" height="50" viewBox="0 0 50 50" fill="none" stroke="#fff" stroke-width="2"><circle cx="25" cy="25" r="7"/><circle cx="25" cy="8" r="4"/><circle cx="25" cy="42" r="4"/><circle cx="8" cy="25" r="4"/><circle cx="42" cy="25" r="4"/><path d="M25 12v6M25 32v6M12 25h6M32 25h6"/></svg></div>
        <h3>2. Mood Insights</h3>
        <p>Our dashboard turns answers into clear trends, so you spot falling morale in a team long before anyone resigns ..</p>
        <a class="btn-dark" href="#">Read More</a>
      </div>
      <div class="card">
        <div class="badge"><svg width="50" height="50" viewBox="0 0 50 50" fill="none" stroke="#fff" stroke-width="2"><circle cx="25" cy="22" r="6"/><path d="M15 44v-6a10 10 0 0 1 20 0v6"/><path d="M10 12c-2-3 2-6 4-3 2-3 6 0 4 3l-4 4zM32 12c-2-3 2-6 4-3 2-3 6 0 4 3l-4 4z"/></svg></div>
        <h3>3. Act &amp; Retain</h3>
        <p>Get simple, tested action plans and recognition tools that lift happiness and keep your best people on board ..</p>
        <a class="btn-dark" href="#">Read More</a>
      </div>
    </div>
  </div>
</section>

<section class="about">
  <div class="about-media" role="img" aria-label="Illustration of relaxed colleagues chatting in an office lounge">
    <svg class="play" width="74" height="74" viewBox="0 0 74 74"><circle cx="37" cy="37" r="33" fill="none" stroke="#fff" stroke-width="5"/><path d="M29 22l23 15-23 15z" fill="#fff"/></svg>
  </div>
  <div class="about-body">
    <h2>About Velrato</h2>
    <p>Velrato helps business owners keep the people they worked so hard to hire. We listen to your employees through quick, anonymous check-ins, show you what drives their mood and loyalty, and guide you through small weekly actions that build a happier workplace. Less turnover, lower hiring costs and teams that want to stay. Watch the short video to see how it works.</p>
    <a class="btn" href="#">Watch A Video</a>
  </div>
</section>

<section class="team">
  <svg class="arrow" style="left:46px" width="16" height="26" viewBox="0 0 16 26"><path d="M13 3L4 13l9 10" fill="none" stroke="#333" stroke-width="3"/></svg>
  <svg class="arrow" style="left:1140px" width="16" height="26" viewBox="0 0 16 26"><path d="M3 3l9 10-9 10" fill="none" stroke="#333" stroke-width="3"/></svg>
  <div class="wrap">
    <h2 class="section-title">Our Team</h2>
    <div class="people">
      <div class="person featured">
        <div class="portrait" role="img" aria-label="Portrait photo of a team member"></div>
        <h4>Graham Pell</h4>
        <p>Founder and workplace psychologist with twenty years of helping teams thrive.</p>
      </div>
      <div class="person p2">
        <div class="portrait" role="img" aria-label="Portrait photo of a team member"></div>
        <h4>Owen Hartley</h4>
        <p>Head of product, building tools your staff enjoy using..</p>
      </div>
      <div class="person p3">
        <div class="portrait" role="img" aria-label="Portrait photo of a team member"></div>
        <h4>Clara Voss</h4>
        <p>Customer success lead, guiding owners step by step..</p>
      </div>
      <div class="person p4">
        <div class="portrait" role="img" aria-label="Portrait photo of a team member"></div>
        <h4>Lucas Brandt</h4>
        <p>Data analyst turning survey answers into clear trends..</p>
      </div>
    </div>
  </div>
</section>

<section class="clients">
  <div class="wrap">
    <h2 class="section-title">Clients</h2>
    <p class="lead">Growing businesses of every size trust Velrato to keep their teams happy, engaged and loyal for the long run ..</p>
    <div class="logos">
      <div><i></i>Norvik</div>
      <div>Halden</div>
      <div><i></i>Quillo</div>
      <div>Brenmark</div>
      <div><i></i>Solvane</div>
    </div>
  </div>
</section>

<section class="testimonials" role="img" aria-label="Testimonials over a dark photo of business people">
  <svg class="arrow" style="left:74px" width="16" height="26" viewBox="0 0 16 26"><path d="M13 3L4 13l9 10" fill="none" stroke="#fff" stroke-width="3"/></svg>
  <svg class="arrow" style="left:1112px" width="16" height="26" viewBox="0 0 16 26"><path d="M3 3l9 10-9 10" fill="none" stroke="#fff" stroke-width="3"/></svg>
  <h2>Testimonials</h2>
  <p class="name">Daniel Orwen</p>
  <blockquote>“ Within three months we could see exactly which teams were struggling and why. We fixed small issues early, our staff feel heard, and we have not lost a single key person since we started.. ”</blockquote>
  <div class="avatar"></div>
</section>

<section class="blog">
  <div class="wrap">
    <h2 class="section-title">Latest Blog Posts</h2>
    <p class="lead">Practical ideas, research and stories on employee morale, engagement and keeping your best people happy at work ..</p>
    <div class="posts">
      <article class="post b1">
        <div class="thumb" role="img" aria-label="Photo of a team meeting around a presentation board"><div class="date"><span>Mar</span><strong>09</strong></div></div>
        <h3>Why good people quit</h3>
        <p>Pay is rarely the real reason. Here are the five quiet signs of a team losing heart, and what to do about each one ..</p>
      </article>
      <article class="post b2">
        <div class="thumb" role="img" aria-label="Photo of a smiling group of coworkers"><div class="date"><span>Mar</span><strong>09</strong></div></div>
        <h3>Small wins, big morale</h3>
        <p>Simple weekly recognition habits cost nothing, take minutes, and lift how valued your staff feel at work ..</p>
      </article>
      <article class="post b3">
        <div class="thumb" role="img" aria-label="Photo of colleagues gathered around a laptop"><div class="date"><span>Mar</span><strong>09</strong></div></div>
        <h3>Reading your pulse data</h3>
        <p>A step by step guide to your first Velrato dashboard, from the mood score to the trends worth acting on ..</p>
      </article>
    </div>
    <div class="cta"><a class="btn" href="#">View All Posts</a></div>
  </div>
</section>

<footer class="site-footer">
  <div class="wrap">
    <div class="foot-logo">Velrato</div>
    <div class="foot-col sitemap">
      <h5>Site Map</h5>
      <ul><li>Home</li><li>What We Do</li><li>Who We Are</li><li>Blog</li><li>Careers</li><li>Contact Us</li></ul>
    </div>
    <div class="foot-col contact">
      <h5>Contact Info</h5>
      <ul>
        <li><svg width="10" height="13" viewBox="0 0 10 13"><path d="M5 0a5 5 0 0 1 5 5c0 3-5 8-5 8S0 8 0 5a5 5 0 0 1 5-5z" fill="#ddd"/><circle cx="5" cy="5" r="2" fill="#141414"/></svg><span>14 Larch Court, Harbour Lane<br>Eastbridge</span></li>
        <li><svg width="12" height="12" viewBox="0 0 12 12"><path d="M2 0l3 3-1.5 2a7 7 0 0 0 3.5 3.5L9 7l3 3-2 2C5 12 0 7 0 2z" fill="#ddd"/></svg><span>1-555-010-4420</span></li>
        <li><svg width="13" height="10" viewBox="0 0 13 10"><rect width="13" height="10" fill="#ddd"/><path d="M0 0l6.5 5L13 0" fill="none" stroke="#141414" stroke-width="1.2"/></svg><span>hello@velrato.example</span></li>
      </ul>
      <span class="map">Map Location</span>
    </div>
    <div class="foot-col subscribe">
      <h5>Email Subscribe</h5>
      <div class="field">Enter Email Address</div>
      <a class="btn" href="#">Sign Up</a>
    </div>
  </div>
</footer>
<div class="bottom-bar">
  <div class="wrap">
    <span>Copyright © 2022. Velrato All Right Reserved</span>
    <div class="social" aria-label="Social links"><span></span><span></span><span></span><span></span><span></span></div>
  </div>
</div>

</body>
</html>
```